Building company buisness cards

We are looking for a sharp modern new look for our business cards.
We are a New Zealand based company that specialises in house and land packages.
We have attached a photo of the current logo and would like to see if it can be improved somehow if needed.
We are open to any colours but we have chosen green at this stage.
Feel free to change the font and make the logo smarter looking.
Play with the colours and see what looks best.

We want a card that looks so good know one will want to throw it away!

Target Market(s)

Home buyers

Industry/Entity Type

Building

Contact Information for Business Card

Derek Tolvane
0217394062
dtolvane@quillmarkhomesteads.co.nz
quillmarkhomesteads.co.nz

Font styles to use
Serif
Sans Serif

Colors

Designer to choose colors to be used in the design.

Requirements
Must have
• Logo and company name on one side, details on the other side
Nice to have
• Color codes for the original green are HEX #4a8028, RGB(74,128,40), CMYK(42,0,69,50)
• Round corners, Raised and/or spot UV

```html
<!DOCTYPE html>
<html lang="en">
<head>
<meta charset="utf-8">
<title>Quillmark Homesteads – Business Card</title>
<link href="https://fonts.googleapis.com/css2?family=Roboto:wght@400;500;700&family=Roboto+Condensed:wght@400&display=swap" rel="stylesheet">
<style>
  :root {
    --brand-green: #4a8028;
    --card-white: #ffffff;
    --text-grey: #555555;
    --divider: #cfcfcf;
    --backdrop: #262626;
    --on-green: #ffffff;
  }
  * { margin: 0; padding: 0; box-sizing: border-box; }
  html, body {
    width: 1125px;
    height: 1200px;
    overflow: hidden;
    background: var(--backdrop);
    font-family: "Roboto", Arial, sans-serif;
  }
  .card {
    position: absolute;
    left: 150px;
    width: 826px;
    height: 471px;
  }
  .card--front { top: 98px; background: var(--card-white); }
  .card--back  { top: 631px; background: var(--brand-green); }

  .brand-name {
    position: absolute;
    left: 40px;
    top: 190px;
    width: 330px;
    text-align: center;
    color: var(--brand-green);
    font-weight: 700;
    line-height: 1;
  }
  .brand-name__top { display: block; font-size: 34px; }
  .brand-name__bottom { display: block; font-size: 40px; margin-top: 4px; }

  .divider {
    position: absolute;
    left: 393px;
    top: 144px;
    width: 1px;
    height: 181px;
    background: var(--divider);
  }

  .contact {
    position: absolute;
    left: 425px;
    top: 165px;
  }
  .contact__name {
    color: var(--brand-green);
    font-weight: 500;
    font-size: 31px;
    letter-spacing: 0.3px;
    margin-bottom: 18px;
  }
  .contact__row {
    display: flex;
    align-items: center;
    height: 26px;
    color: var(--text-grey);
    font-size: 20px;
  }
  .contact__row--email { font-family: "Roboto Condensed", Arial, sans-serif; }
  .contact__icon {
    width: 18px;
    height: 18px;
    margin-right: 12px;
    flex: none;
    fill: var(--brand-green);
  }

  .back-brand {
    position: absolute;
    left: 0;
    top: 170px;
    width: 100%;
    text-align: center;
    color: var(--on-green);
    font-weight: 700;
    line-height: 1.05;
  }
  .back-brand span { display: block; font-size: 46px; }
  .back-web {
    position: absolute;
    left: 0;
    top: 404px;
    width: 100%;
    text-align: center;
    color: var(--on-green);
    opacity: 0.85;
    font-size: 19px;
    letter-spacing: 5px;
  }
</style>
</head>
<body>
  <section class="card card--front">
    <div class="brand-name">
      <span class="brand-name__top">quillmark</span>
      <span class="brand-name__bottom">homesteads.</span>
    </div>
    <div class="divider"></div>
    <div class="contact">
      <div class="contact__name">DEREK TOLVANE</div>
      <div class="contact__row">
        <svg class="contact__icon" viewBox="0 0 24 24" aria-hidden="true"><path d="M6.6 10.8c1.4 2.8 3.8 5.1 6.6 6.6l2.2-2.2c.3-.3.7-.4 1-.2 1.1.4 2.3.6 3.6.6.6 0 1 .4 1 1V20c0 .6-.4 1-1 1C10.6 21 3 13.4 3 4c0-.6.4-1 1-1h3.5c.6 0 1 .4 1 1 0 1.3.2 2.5.6 3.6.1.3 0 .7-.2 1z"/></svg>
        0217394062
      </div>
      <div class="contact__row contact__row--email">
        <svg class="contact__icon" viewBox="0 0 24 24" aria-hidden="true"><path d="M2 6h20v12H2z" fill="none"/><path d="M2 6.5 12 13l10-6.5V18H2z M2.5 6h19L12 12.2z"/></svg>
        dtolvane@quillmarkhomesteads.co.nz
      </div>
      <div class="contact__row">
        <svg class="contact__icon" viewBox="0 0 24 24" aria-hidden="true"><circle cx="12" cy="12" r="10"/><path d="M7 7c2 0 3 1 3 2.5S8 11 8 13s2 2 2 4M15 5c-1 1.5 0 3 1.5 3.5s2 2 1 3.5-.5 3 1 3.5" stroke="#fff" stroke-width="1.6" fill="none"/></svg>
        quillmarkhomesteads.co.nz
      </div>
    </div>
  </section>

  <section class="card card--back">
    <div class="back-brand">
      <span>quillmark</span>
      <span>homesteads.</span>
    </div>
    <div class="back-web">www.quillmarkhomesteads.co.nz</div>
  </section>
</body>
</html>
```